A start-up named "lumerova" - a clinical research organization needs a new PowerPoint design

We need a new PowerPoint Design (incl. business card and stationery design) for an early-stage start-up named "lumerova" seeking to build an ecosystem/ strategic partner alliances or consortium of committed and active collaborators to guide important components of the clinical trial.

Our ultimate goal is to avoid false neutrals – therapies that have not been and may never be evaluated in clinical trials due to the costs and/ or complexity.

The final design should highlight our patient-centric approach, innovative study design supported with the novel AI platform to make a stronger impact on patient lives.

Please see the attached brief for more details.
Updates

Requesting the proposals on color-coding, business-card designs, clinical research visuals, and icons as well as stationery design.

Target Market(s)

Pharma/ Biotech Executives
Medical Institutions
Clinical Trial Participants (Patients)

Colors
e34398

Requirements
Must have
• Use the Color Version of purple/ magenta logo

```html
<!DOCTYPE html>
<html lang="en">
<head>
<meta charset="utf-8">
<title>lumerova – Presentation</title>
<link rel="stylesheet" href="https://fonts.googleapis.com/css2?family=Quicksand:wght@700&family=Roboto:wght@400&display=swap">
<style>
:root{
  --magenta:#e34398;
  --magenta-band:#d5388c;
  --maroon:#4a0a2c;
  --navy:#061627;
  --navy-2:#0c3a5e;
  --ink:#2b2b2b;
  --white:#ffffff;
  --mist:#eef1f4;
}
*{margin:0;padding:0;box-sizing:border-box}
html,body{width:1200px;height:4383px;overflow:hidden}
body{font-family:'Roboto',sans-serif;color:var(--ink);background:var(--white)}
.slide{position:absolute;left:0;width:1200px;overflow:hidden}
.heading{font-family:'Quicksand',sans-serif;font-weight:700;position:absolute;line-height:1.05}
.mark{display:inline-block;width:.32em;height:.32em;background:currentColor;margin-left:.12em;vertical-align:.55em;opacity:.9}
.copy{position:absolute;font-size:16px;line-height:25px}
.copy p+p{margin-top:25px}
.photo{position:absolute}
.bullets{list-style:none;position:absolute;font-size:16px;line-height:25px;color:var(--white)}
.bullets li{position:relative;padding-left:38px}
.bullets li svg{position:absolute;left:0;top:6px}

/* hero */
.hero{top:0;height:626px;background:radial-gradient(circle at 1000px 320px,#f04aa3 0,#c82a7c 28%,#7d1048 60%,var(--maroon) 100%)}
.hero .brand{position:absolute;left:90px;top:262px;font-family:'Quicksand',sans-serif;font-weight:700;font-size:86px;color:var(--white);letter-spacing:-1px}
.hero .brand .mark{background:var(--white)}
.hero .emblem{position:absolute;left:1050px;top:220px;width:90px;height:190px;border-radius:45px;background:linear-gradient(#f7b7d8,#e679b3);opacity:.55}

/* intro */
.intro{top:626px;height:628px;background:radial-gradient(ellipse at 50% 60%,#ffffff 0,#f3f5f7 55%,#dde3e8 100%)}
.intro .heading{left:0;width:1200px;text-align:center;top:122px;font-size:56px;color:var(--magenta)}
.intro .copy{left:145px;width:912px;top:208px;text-align:center;font-size:15.5px}
.intro .copy p+p{text-align:justify}

/* ecosystem */
.ecosystem{top:1254px;height:623px;background:var(--magenta-band)}
.ecosystem .heading{left:90px;top:122px;font-size:58px;color:var(--white)}
.ecosystem .bullets{left:90px;top:328px;width:580px}

/* guide */
.guide{top:1877px;height:627px;background:linear-gradient(160deg,var(--navy) 0,#0a2a47 55%,var(--navy-2) 100%)}
.guide .heading{left:594px;top:76px;font-size:56px;color:var(--magenta)}
.guide .copy{left:596px;width:497px;top:208px;color:var(--white);text-align:justify;font-size:15.5px}

/* what we do */
.work{top:2504px;height:628px;background:linear-gradient(90deg,#f7f1f5 0,#eef0f3 45%,#c9ced4 100%)}
.work .heading{left:87px;top:176px;font-size:56px;color:var(--magenta)}
.work .copy{left:87px;width:465px;top:252px;text-align:justify;font-size:15.5px}

/* summary */
.summary{top:3132px;height:625px;background:var(--magenta-band)}
.summary .heading{left:90px;top:108px;font-size:58px;color:var(--white)}
.summary .bullets{left:90px;top:200px;width:1022px;font-size:15.5px}

/* thanks */
.thanks{top:3757px;height:626px;background:linear-gradient(180deg,#6f8396 0,#4e6378 50%,#3a4c5e 100%)}
.thanks .heading{left:0;width:1200px;text-align:center;top:260px;font-size:86px;color:var(--white)}
</style>
</head>
<body>

<section class="slide hero" role="img" aria-label="Glowing magenta particle field background">
  <div class="brand">lumerova<span class="mark"></span></div>
  <div class="emblem" role="img" aria-label="DNA helix illustration"></div>
</section>

<section class="slide intro" role="img" aria-label="Soft focus photo of a doctor presenting an open hand">
  <h2 class="heading">Introduction<span class="mark"></span></h2>
  <div class="copy">
    <p>Lorem ipsum dolor sit amet, consectetur adipiscing elit, sed do eiusmod tempor incididunt ut labore et dolore magna aliqua. Ut enim ad minim veniam, quis nostrud exercitation ullamco laboris nisi ut aliquip ex ea commodo consequat. Duis aute irure dolor in reprehenderit in voluptate velit esse cillum dolore eu fugiat nulla pariatur. Excepteur sint occæcat cupidatat non proident, sunt in culpa qui officia deserunt mollit anim id est laborum.</p>
    <p>Sed ut perspiciatis unde omnis iste natus error sit voluptatem accusantium doloremque laudantium, totam rem aperiam, eaque ipsa quæ ab illo inventore veritatis et quasi architecto beatæ vitæ dicta sunt explicabo. Nemo enim ipsam voluptatem quia voluptas sit aspernatur aut odit aut fugit, sed quia consequuntur magni dolores eos qui ratione voluptatem sequi nesciunt. Neque porro quisquam est, qui dolorem ipsum quia dolor sit amet, consectetur, adipisci velit, sed quia non numquam eius modi tempora incidunt ut labore et dolore magnam aliquam quærat voluptatem. Ut enim ad minima veniam, quis nostrum exercitationem ullam corporis suscipit laboriosam, nisi ut aliquid ex ea commodi consequatur? Quis autem vel eum iure reprehenderit qui in ea voluptate velit esse quam nihil molestiæ consequatur, vel illum qui dolorem eum fugiat quo voluptas nulla pariatur</p>
  </div>
</section>

<svg width="0" height="0" style="position:absolute">
  <defs>
    <symbol id="bullet" viewBox="0 0 14 14">
      <circle cx="7" cy="7" r="7" fill="#fff"/>
      <path d="M3.5 7h6M7 4.2 9.8 7 7 9.8" fill="none" stroke="#d5388c" stroke-width="1.6" stroke-linecap="round" stroke-linejoin="round"/>
    </symbol>
  </defs>
</svg>

<section class="slide ecosystem">
  <h2 class="heading">An Ecosystem/<br>Strategic Partner<span class="mark"></span><br>Alliances</h2>
  <ul class="bullets">
    <li><svg width="14" height="14"><use href="#bullet"/></svg>Lorem ipsum dolor sit amet, consectetur adipiscing elit, sed do eiusmod tempor incididunt ut labore et dolore magna aliqua.</li>
    <li><svg width="14" height="14"><use href="#bullet"/></svg>Ut enim ad minim veniam, quis nostrud exercitation ullamco laboris nisi</li>
    <li><svg width="14" height="14"><use href="#bullet"/></svg>Ut aliquip ex ea commodo consequat. Duis aute irure dolor in</li>
    <li><svg width="14" height="14"><use href="#bullet"/></svg>Reprehenderit in voluptate velit esse cillum dolore eu fugiat nulla pariatur.</li>
    <li><svg width="14" height="14"><use href="#bullet"/></svg>Excepteur sint occæcat cupidatat non proident, sunt in culpa qui officia</li>
    <li><svg width="14" height="14"><use href="#bullet"/></svg>Deserunt mollit anim id est laborum.</li>
  </ul>
  <div class="photo" style="left:708px;top:0;width:284px;height:264px;background:linear-gradient(160deg,#cfe3f2,#5e8fb8)" role="img" aria-label="Gloved hand holding blood sample tubes in a rack"></div>
  <div class="photo" style="left:1059px;top:0;width:141px;height:206px;background:linear-gradient(160deg,#e9edf0,#8a9aa6)" role="img" aria-label="Doctors smiling at a laptop"></div>
  <div class="photo" style="left:683px;top:389px;width:288px;height:234px;background:linear-gradient(160deg,#f1f3f5,#9fa9b2)" role="img" aria-label="Researcher looking into a microscope"></div>
  <div class="photo" style="left:1016px;top:291px;width:184px;height:288px;background:linear-gradient(160deg,#e7eef3,#7ea3bf)" role="img" aria-label="Scientist holding a flask in a laboratory"></div>
</section>

<section class="slide guide" role="img" aria-label="Dark blue background with glowing hexagon network">
  <div class="photo" style="left:85px;top:80px;width:434px;height:477px;border-radius:50%;background:radial-gradient(circle,rgba(90,170,230,.35),rgba(12,42,71,0) 70%)" role="img" aria-label="Cluster of circular medical icons: heart rate, brain, doctor, flask, hospital bed, eye, caduceus"></div>
  <h2 class="heading">Important Guide<span class="mark"></span></h2>
  <div class="copy">
    <p>Lorem ipsum dolor sit amet, consectetur adipiscing elit, sed do eiusmod tempor incididunt ut labore et dolore magna aliqua.</p>
    <p>Ut enim ad minim veniam, quis nostrud exercitation ullamco laboris nisi ut aliquip ex ea commodo consequat. Duis aute irure dolor in reprehenderit in voluptate velit esse cillum dolore eu fugiat nulla pariatur. Excepteur sint occæcat cupidatat non proident, sunt in culpa qui officia deserunt mollit anim id est laborum.</p>
    <p>&nbsp;Excepteur sint occæcat cupidatat non proident, sunt in culpa qui officia deserunt mollit anim id est laborum. Excepteur sint occæcat cupidatat non proident, sunt in culpa qui officia deserunt mollit anim id est laborum.</p>
  </div>
</section>

<section class="slide work" role="img" aria-label="Scientist in safety glasses looking into a microscope">
  <h2 class="heading">What we Do<span class="mark"></span></h2>
  <div class="copy">
    <p>Lorem ipsum dolor sit amet, consectetur adipiscing elit, sed do eiusmod tempor incididunt ut labore et dolore magna aliqua.</p>
    <p>Ut enim ad minim veniam, quis nostrud exercitation ullamco laboris nisi ut aliquip ex ea commodo consequat. Duis aute irure dolor in reprehenderit in voluptate velit esse cillum dolore eu fugiat nulla pariatur. Excepteur sint occæcat cupidatat non proident, sunt in culpa qui officia deserunt mollit anim id est laborum.</p>
  </div>
</section>

<section class="slide summary">
  <h2 class="heading">General Summary<span class="mark"></span></h2>
  <ul class="bullets">
    <li><svg width="14" height="14"><use href="#bullet"/></svg>Lorem ipsum dolor sit amet, consectetur adipiscing elit, sed do eiusmod tempor incididunt ut labore et dolore magna aliqua. Ut enim ad minim veniam, quis nostrud exercitation ullamco laboris nisi Ut aliquip ex ea commodo consequat. Duis aute irure dolor in</li>
    <li><svg width="14" height="14"><use href="#bullet"/></svg>Reprehenderit in voluptate velit esse cillum dolore eu fugiat nulla pariatur. Excepteur sint occæcat cupidatat non proident, sunt in culpa qui officia Deserunt mollit anim id est laborum.</li>
    <li><svg width="14" height="14"><use href="#bullet"/></svg>Sed ut perspiciatis unde omnis iste natus error sit voluptatem accusantium doloremque laudantium, totam rem aperiam, eaque ipsa quæ ab illo inventore veritatis et quasi architecto beatæ vitæ dicta sunt explicabo. Nemo enim ipsam voluptatem quia voluptas sit aspernatur aut odit aut fugit, sed quia consequuntur magni dolores eos qui ratione voluptatem sequi nesciunt.</li>
    <li><svg width="14" height="14"><use href="#bullet"/></svg>Neque porro quisquam est, qui dolorem ipsum quia dolor sit amet, consectetur, adipisci velit, sed quia non numquam eius modi tempora incidunt ut labore et dolore magnam aliquam quærat voluptatem.</li>
    <li><svg width="14" height="14"><use href="#bullet"/></svg>Ut enim ad minima veniam, quis nostrum exercitationem ullam corporis suscipit laboriosam, nisi ut aliquid ex ea commodi consequatur? Quis autem vel eum iure reprehenderit qui in ea voluptate velit esse quam nihil molestiæ consequatur, vel illum qui dolorem eum fugiat quo voluptas nulla pariatur</li>
  </ul>
</section>

<section class="slide thanks" role="img" aria-label="Laboratory glassware and a microscope in blue-grey tones">
  <h2 class="heading">Thank You</h2>
</section>

</body>
</html>
```